Business Card for a mobile physiotherapy company

I need a layout for a business card for a mobile physiotherapy company.
Slogan is "Mobile Physiotherapy - Your Road To Recovery"
Phone number is 867-555-0142
Email VardenTherapy@postnest.ca (subject to change with website)
Website www.VardenTherapy.ca
My name and credentials: Luke Varden Luke Varden, BSc(kin), MPT, CAFCI, IMS
Information maybe included: Direct Billing, Services including Physiotherapy, IMS, acupuncture
Maybe include facebook and instagram logos
One side with the logo clean and sharp
Other side with details, try not to look too busy, keep everything concise

```html
<!DOCTYPE html>
<html lang="en">
<head>
<meta charset="utf-8">
<title>Varden Therapy – Business Card</title>
<link rel="stylesheet" href="https://fonts.googleapis.com/css2?family=Open+Sans:ital,wght@0,400;0,600;0,700;1,400&display=swap">
<style>
  :root {
    --bg: #2b2c30;
    --card-white: #ffffff;
    --pine: #0f5e50;
    --navy: #1f4f8a;
    --teal-top: #0c4868;
    --teal-bottom: #137a6c;
    --on-dark: #ffffff;
  }
  * { box-sizing: border-box; margin: 0; padding: 0; }
  html, body { width: 1200px; height: 900px; overflow: hidden; }
  body {
    background: var(--bg);
    font-family: "Open Sans", Arial, sans-serif;
    display: flex;
    align-items: center;
    justify-content: center;
    gap: 40px;
  }
  .card {
    position: relative;
    width: 540px;
    height: 310px;
    border-radius: 24px;
    overflow: hidden;
  }

  /* details side */
  .card-details { background: var(--card-white); }
  .person { position: absolute; left: 36px; top: 28px; }
  .person-name { color: var(--pine); font-weight: 700; font-size: 25px; line-height: 1.1; }
  .person-credentials { color: var(--navy); font-size: 14px; margin-top: 3px; }
  .contact-list { position: absolute; left: 36px; top: 100px; list-style: none; }
  .contact-item {
    display: flex; align-items: center; gap: 10px;
    color: var(--navy); font-size: 14.5px; font-weight: 600;
    height: 27px;
  }
  .contact-icon { width: 20px; height: 20px; flex: none; }

  .brand-block {
    position: absolute; right: 36px; top: 116px;
    display: flex; flex-direction: column; align-items: flex-end; gap: 18px;
  }
  .brand-mark { display: flex; align-items: center; gap: 8px; }
  .brand-dot { width: 12px; height: 12px; border-radius: 50%; background: var(--pine); flex: none; }
  .brand-name { color: var(--pine); font-weight: 700; font-size: 20px; line-height: 1; white-space: nowrap; }
  .social-row { display: flex; gap: 10px; }
  .social-dot { width: 22px; height: 22px; border-radius: 50%; background: var(--navy); }

  .slogan-band {
    position: absolute; left: 0; right: 0; top: 226px; height: 28px;
    background: var(--pine);
    color: var(--on-dark); font-style: italic; font-size: 14px;
    display: flex; align-items: center; justify-content: flex-end; padding-right: 36px;
  }
  .services {
    position: absolute; left: 0; right: 36px; top: 262px;
    text-align: right; color: var(--navy); font-style: italic; font-size: 13.5px;
  }

  /* logo side */
  .card-logo {
    background: linear-gradient(160deg, var(--teal-top) 0%, var(--teal-bottom) 100%);
    display: flex; align-items: center; justify-content: center;
  }
  .card-logo .brand-mark { gap: 14px; }
  .card-logo .brand-dot { width: 20px; height: 20px; background: var(--on-dark); }
  .card-logo .brand-name { color: var(--on-dark); font-size: 40px; }
</style>
</head>
<body>

<section class="card card-details">
  <div class="person">
    <h1 class="person-name">Luke Varden</h1>
    <p class="person-credentials">BSc(kin), MPT, CAFCI, IMS</p>
  </div>

  <ul class="contact-list">
    <li class="contact-item">
      <svg class="contact-icon" viewBox="0 0 20 20" aria-hidden="true">
        <circle cx="10" cy="10" r="10" fill="#0f5e50"/>
        <path d="M7 5.5l1.6 2.6-1 1a6 6 0 0 0 3.3 3.3l1-1 2.6 1.6-.8 1.8c-4.2.2-7.9-3.5-7.7-7.7z" fill="#fff"/>
      </svg>
      867-555-0142
    </li>
    <li class="contact-item">
      <svg class="contact-icon" viewBox="0 0 20 20" aria-hidden="true">
        <circle cx="10" cy="10" r="10" fill="#0f5e50"/>
        <rect x="5" y="6.5" width="10" height="7" rx="1" fill="#fff"/>
        <path d="M5.3 7l4.7 3.6L14.7 7" fill="none" stroke="#0f5e50" stroke-width="1.1"/>
      </svg>
      VardenTherapy@postnest.ca
    </li>
    <li class="contact-item">
      <svg class="contact-icon" viewBox="0 0 20 20" aria-hidden="true">
        <circle cx="10" cy="10" r="10" fill="#0f5e50"/>
        <g fill="none" stroke="#fff" stroke-width="1.1">
          <circle cx="10" cy="10" r="5"/>
          <ellipse cx="10" cy="10" rx="2.2" ry="5"/>
          <path d="M5 10h10"/>
        </g>
      </svg>
      www.VardenTherapy.ca
    </li>
  </ul>

  <div class="brand-block">
    <div class="brand-mark">
      <span class="brand-dot" aria-hidden="true"></span>
      <span class="brand-name">Varden Therapy</span>
    </div>
    <div class="social-row" aria-hidden="true">
      <span class="social-dot"></span>
      <span class="social-dot"></span>
    </div>
  </div>

  <p class="slogan-band">Mobile Physiotherapy - Your Road To Recovery</p>
  <p class="services">Direct Billing. Services including Physiotherapy, IMS, Acupuncture</p>
</section>

<section class="card card-logo">
  <div class="brand-mark">
    <span class="brand-dot" aria-hidden="true"></span>
    <span class="brand-name">Varden Therapy</span>
  </div>
</section>

</body>
</html>
```